Kovát Lillas Physiotherapy Business Card Vienna

We need a business card design for a newly created Physiotherapy company based in Vienna Austria.
We seek a simple, modern, minimalist design without too much color variation. The font should look young/fresh, but definitely not childish or so. Since we are a starting Business, we currently haven't got a logo, if you feel like a logo would fit your design, feel free to use one, but it's not necessary.
Target Market(s)
Healthcare, young and elderly people with mobility issues
Industry/Entity Type
Health And Wellness
Contact Information for Business Card
Name: Lilla Kovát
Title description: Physiotherapist
Phone num: +43 664 2951 4086
e-mail: lilla.praxis@bluemail.example
Colors
Designer to choose colors to be used in the design.
Requirements
Must have
- Final design language must be in German, basically, the Title Description needs to be "Physiotherapeutin" the other details remain as in the English Language.
Nice to have
- Simple, modern, minimalist design
Should not have
- too many colors, Obvious use of a skeleton, skull, spline

```html
<!DOCTYPE html>
<html lang="de">
<head>
<meta charset="utf-8">
<title>Lilla Kovát – Physiotherapeutin – Visitenkarte</title>
<link rel="stylesheet" href="https://fonts.googleapis.com/css2?family=Saira+Condensed:wght@300;400;700&family=Saira+Extra+Condensed:wght@400;700&display=swap">
<style>
  :root {
    --backdrop: #e6ecea;
    --card: #ffffff;
    --ink: #0b0b0b;
    --card-edge: #d6d6d6;
  }
  * { margin: 0; padding: 0; box-sizing: border-box; }
  html, body {
    width: 1200px;
    height: 1200px;
    overflow: hidden;
    background: var(--backdrop);
  }
  .canvas {
    position: relative;
    width: 1200px;
    height: 1200px;
  }
  .card {
    position: absolute;
    left: 294px;
    top: 124px;
    width: 614px;
    height: 952px;
    background: var(--card);
    border: 1px solid var(--card-edge);
    color: var(--ink);
    overflow: hidden;
  }
  .headline {
    position: absolute;
    left: 60px;
    top: 56px;
    width: 500px;
    font-family: "Saira Condensed", "Saira Extra Condensed", "Arial Narrow", sans-serif;
    font-size: 104px;
    line-height: 96px;
    text-transform: uppercase;
    letter-spacing: 0;
  }
  .headline .profession { font-weight: 700; display: block; }
  .headline .person { font-weight: 400; display: block; }
  .contact {
    position: absolute;
    left: 58px;
    top: 688px;
    font-family: "Saira Condensed", "Arial Narrow", sans-serif;
    font-weight: 400;
    list-style: none;
  }
  .contact li { display: block; white-space: nowrap; }
  .contact .role { font-size: 40px; line-height: 64px; letter-spacing: 0.14em; }
  .contact .phone { font-size: 42px; line-height: 64px; letter-spacing: 0.1em; }
  .contact .email { font-size: 32px; line-height: 64px; letter-spacing: 0.1em; }
</style>
</head>
<body>
<main class="canvas">
  <article class="card">
    <h1 class="headline">
      <span class="profession">Physiothe</span>
      <span class="profession">rapeutin</span>
      <span class="person">Lilla</span>
      <span class="person">Kovát</span>
    </h1>
    <ul class="contact">
      <li class="role">Physiotherapist</li>
      <li class="phone">+43 664 2951 4086</li>
      <li class="email">lilla.praxis@bluemail.example</li>
    </ul>
  </article>
</main>
</body>
</html>
```